Cedarvale Ridge College

We are looking to update our current webpage at www.cedarvaleridge.ca. We would like to make it modern, fresh and appealing to students. We want to keep our logo the same with the logo colours blended in as the primary colours and focus. We are open to reconfiguring content as well.
Reason: Hi, In the next 3 days we will have narrowed our search to 3 designs and will make a choice before the final deadline...
College

```html
<!DOCTYPE html>
<html lang="en">
<head>
<meta charset="utf-8">
<title>Cedarvale Ridge College</title>
<link href="https://fonts.googleapis.com/css2?family=Open+Sans:wght@400;600;700;800&display=swap" rel="stylesheet">
<style>
:root{
  --navy:#1c2b5e;
  --navy-dark:#14204a;
  --navy-deep:#0e1735;
  --ink:#222a3d;
  --muted:#6b6f7a;
  --light:#eeeff1;
  --white:#ffffff;
  --line:#d4d6dc;
}
*{box-sizing:border-box;margin:0;padding:0}
html,body{width:1200px;height:2820px;overflow:hidden}
body{font-family:"Open Sans",Arial,sans-serif;color:var(--ink);background:var(--white);position:relative}
section,header,footer{position:absolute;left:0;width:1200px}
.btn{display:inline-block;background:var(--navy);color:var(--white);font-size:13px;font-weight:600;padding:8px 22px;border-radius:4px}
.title{font-size:30px;font-weight:700;color:var(--navy);text-align:center}
.copy{font-size:13px;line-height:1.65;color:var(--muted)}

/* header */
.site-header{top:0;height:120px;background:var(--white)}
.brand{position:absolute;left:110px;top:30px;display:flex;align-items:center;gap:12px}
.brand-dot{width:38px;height:38px;border-radius:50%;background:var(--navy)}
.brand-name{font-size:26px;font-weight:700;color:var(--navy);line-height:1.05;width:230px}
.utility{position:absolute;right:60px;top:0;display:flex;gap:3px}
.utility span{background:var(--navy);color:var(--white);font-size:11px;font-weight:600;padding:6px 14px;border-radius:0 0 4px 4px}
.main-nav{top:120px;height:40px;background:var(--navy);display:flex;padding-left:110px}
.main-nav a{color:var(--white);font-size:13px;font-weight:600;text-decoration:none;padding:0 18px;line-height:40px}
.main-nav a.active{background:var(--navy-dark)}

/* hero */
.hero{top:160px;height:510px}
.hero-photo{position:absolute;inset:0;background:linear-gradient(180deg,#1f2f4e 0%,#33485a 45%,#4c5a49 75%,#2d3529 100%)}
.hero-shade{position:absolute;inset:0;background:rgba(10,18,40,.35)}
.hero-inner{position:absolute;left:0;right:0;top:220px;text-align:center;color:var(--white)}
.hero h1{font-size:30px;font-weight:800;letter-spacing:.5px}
.hero p{font-size:13px;margin-top:8px;opacity:.9}
.signup{display:flex;justify-content:center;gap:14px;margin-top:26px}
.signup .field{width:210px;height:34px;background:var(--white);border-radius:3px;color:#999;font-size:12px;text-align:left;padding:9px 12px}
.signup .join{height:34px;padding:0 20px;background:var(--navy);color:var(--white);font-size:13px;font-weight:700;line-height:34px;border-radius:3px}
.scroll-down{position:absolute;left:578px;top:440px}

/* welcome */
.welcome{top:670px;height:330px;text-align:center}
.welcome .title{margin-top:50px}
.welcome .copy{width:900px;margin:20px auto 22px}

/* videos */
.videos{top:1000px;height:300px;text-align:center;color:var(--white)}
.videos-photo{position:absolute;inset:0;background:linear-gradient(90deg,#2b3a33 0%,#3e4d45 50%,#25322c 100%)}
.videos-shade{position:absolute;inset:0;background:rgba(8,14,22,.55)}
.videos-inner{position:relative;padding-top:52px}
.videos h2{font-size:28px;font-weight:700}
.videos p{width:900px;margin:16px auto 24px;font-size:13px;line-height:1.65;opacity:.9}

/* campus */
.campus{top:1300px;height:500px}
.section-head{display:flex;align-items:center;justify-content:center;gap:20px;margin-top:40px}
.section-head::before,.section-head::after{content:"";width:300px;height:1px;background:var(--line)}
.section-head h2{font-size:28px;font-weight:700;color:var(--navy)}
.campus-cards{display:flex;justify-content:center;gap:100px;margin-top:40px}
.campus-card{width:260px;text-align:center}
.campus-card .thumb{height:170px;border:4px solid var(--white);box-shadow:0 0 0 1px var(--line)}
.thumb-map{background:linear-gradient(135deg,#3f4f7a,#6b7aa8)}
.thumb-directions{background:linear-gradient(135deg,#dfe6d7,#b9c9e0)}
.thumb-tour{background:linear-gradient(135deg,#8a6d52,#c7b59a)}
.campus-card h3{font-size:17px;font-weight:700;color:var(--navy);margin:16px 0 6px}
.campus-card .copy{margin-bottom:14px}

/* admissions & news */
.info{top:1800px;height:420px;background:var(--light)}
.admissions{position:absolute;left:130px;top:44px;width:420px}
.news{position:absolute;left:605px;top:44px;width:470px}
.info h2{font-size:28px;font-weight:700;color:var(--navy)}
.admission-list{list-style:none;margin-top:22px}
.admission-list li{font-size:13px;color:var(--ink);line-height:30px;display:flex;align-items:center;gap:10px}
.admission-list li::before{content:"";width:6px;height:6px;background:var(--navy);border-radius:50%}
.news-items{display:flex;gap:30px;margin-top:22px}
.news-item{width:220px}
.news-item .thumb{height:110px;border:4px solid var(--white)}
.news-a{background:linear-gradient(135deg,#9fb4cf,#e3e7ee)}
.news-b{background:linear-gradient(135deg,#c9b9a5,#8ea3c2)}
.news-item .date{font-size:13px;font-weight:700;color:var(--navy);margin-top:12px}
.news-item .copy{color:var(--ink);margin-top:4px}
.news-item .more{font-size:13px;font-weight:600;color:var(--navy);margin-top:4px}

/* contact */
.contact{top:2220px;height:560px;background:var(--navy);color:var(--white)}
.contact-head{text-align:center;padding-top:34px}
.contact-head h2{font-size:26px;font-weight:700;margin-top:12px}
.contact-head p{font-size:13px;line-height:1.5;opacity:.85;margin-top:6px}
.contact-cols{position:absolute;top:210px;left:130px;display:flex;gap:60px}
.contact-cols h3{font-size:19px;font-weight:600;margin-bottom:16px}
.question{width:280px}
.question .field{height:32px;background:var(--white);border-radius:3px;margin-bottom:12px;color:#999;font-size:12px;padding:8px 12px}
.question .message{height:92px}
.question .send{display:inline-block;background:var(--white);color:var(--navy);font-size:13px;font-weight:700;padding:7px 20px;border-radius:3px}
.location{width:330px}
.location .map{height:250px;background:linear-gradient(135deg,#d9e2d0,#eef0f4 55%,#c9d6e6);border:4px solid var(--white)}
.find{width:240px}
.find-row{display:flex;gap:12px;font-size:13px;line-height:1.5;margin-bottom:10px;align-items:flex-start}
.find-row svg{flex:none;margin-top:2px}
.socials{display:flex;gap:8px;margin-top:12px}
.socials span{width:26px;height:26px;background:var(--white);border-radius:3px}

/* footer */
.site-footer{top:2780px;height:40px;background:var(--navy-deep);color:#b8bfd4;font-size:11px;text-align:center;line-height:40px}
</style>
</head>
<body>

<header class="site-header">
  <div class="brand">
    <span class="brand-dot"></span>
    <span class="brand-name">Cedarvale Ridge College</span>
  </div>
  <div class="utility">
    <span>Apply Today</span><span>Donate</span><span>Library</span><span>Text For Info</span>
  </div>
</header>

<nav class="main-nav" style="position:absolute;top:120px;left:0;width:1200px">
  <a class="active">Home</a><a>About Us</a><a>Consult Cedarvale</a><a>Current students</a><a>Alumni</a><a>Supporters</a><a>News &amp; Event</a><a>Cedarvale Park</a>
</nav>

<section class="hero">
  <div class="hero-photo" role="img" aria-label="Campus buildings lit at dusk among evergreen trees"></div>
  <div class="hero-shade"></div>
  <div class="hero-inner">
    <h1>WE WILL HELP YOU TO UNDERSTAND FRIENDLY COMPASS</h1>
    <p>Lorem ipsum dolor sit amet, consectetur adipiscing elit. Aenean euismod bibendum laoreet proin gravida dolor.</p>
    <div class="signup">
      <div class="field">Name</div>
      <div class="field">Email Address</div>
      <div class="join">JOIN NOW ›</div>
    </div>
  </div>
  <svg class="scroll-down" width="44" height="44" viewBox="0 0 44 44"><circle cx="22" cy="22" r="20" fill="none" stroke="#fff" stroke-width="2"/><path d="M14 19l8 8 8-8" fill="none" stroke="#fff" stroke-width="2.5"/></svg>
</section>

<section class="welcome">
  <h2 class="title">Welcome Cedarvale Ridge College</h2>
  <p class="copy">Lorem ipsum dolor sit amet, consectetur adipiscing elit. Aenean et dignissim sem, interdum risus. Vestibulum consectetur mi mollis diam auctor adipiscing. Vestibulum at urna nec nibh adipiscing facilisis. Etiam auctor porta lacus ac luctus. Praesent ac libero fermentum, rhoncus magna a, dapibus mauris. Nam ut auctor justo. Sed ante odio, luctus quis neque nec, adipiscing eleifend arcu. Integer nunc turpis, porttitor at lorem id. Etiam auctor porta lacus ac luctus. Praesent ac libero fermentum, rhoncus magna.</p>
  <span class="btn">Read More</span>
</section>

<section class="videos">
  <div class="videos-photo" role="img" aria-label="Dim view of the college entrance sign at night"></div>
  <div class="videos-shade"></div>
  <div class="videos-inner">
    <h2>Cedarvale Videos</h2>
    <p>Lorem ipsum dolor sit amet, consectetur adipiscing elit. Aenean et dignissim sem, interdum risus. Vestibulum consectetur mi mollis diam auctor adipiscing. Vestibulum at urna nec nibh adipiscing facilisis. Etiam auctor porta lacus ac luctus. Praesent ac libero fermentum, rhoncus magna a, dapibus mauris nam ut auctor.</p>
    <svg width="56" height="56" viewBox="0 0 56 56"><circle cx="28" cy="28" r="26" fill="none" stroke="#fff" stroke-width="3"/><path d="M22 17l17 11-17 11z" fill="#fff"/></svg>
  </div>
</section>

<section class="campus">
  <div class="section-head"><h2>Our Campus</h2></div>
  <div class="campus-cards">
    <div class="campus-card">
      <div class="thumb thumb-map" role="img" aria-label="Aerial campus map with location markers"></div>
      <h3>Campus Map</h3>
      <p class="copy">Lorem ipsum dolor sit amet, consectetur adipiscing elit. Aenean et dignissim sem, interdum risus vestibulum.</p>
      <span class="btn">Read More</span>
    </div>
    <div class="campus-card">
      <div class="thumb thumb-directions" role="img" aria-label="Street map showing directions to campus"></div>
      <h3>Map &amp; Directions</h3>
      <p class="copy">Lorem ipsum dolor sit amet, consectetur adipiscing elit. Aenean et dignissim sem, interdum risus vestibulum.</p>
      <span class="btn">Read More</span>
    </div>
    <div class="campus-card">
      <div class="thumb thumb-tour" role="img" aria-label="Interior of the campus chapel with rows of seats"></div>
      <h3>Photo Tour</h3>
      <p class="copy">Lorem ipsum dolor sit amet, consectetur adipiscing elit. Aenean et dignissim sem, interdum risus vestibulum.</p>
      <span class="btn">Read More</span>
    </div>
  </div>
</section>

<section class="info">
  <div class="admissions">
    <h2>Our Admissions</h2>
    <ul class="admission-list">
      <li>Download The Full Catalogue</li>
      <li>Apply Today (Application Package)</li>
      <li>Information Request</li>
      <li>Browse our Programs</li>
      <li>Download Forms</li>
      <li>Admissions Information</li>
      <li>Campus Directory</li>
    </ul>
  </div>
  <div class="news">
    <h2>News &amp; Event</h2>
    <div class="news-items">
      <div class="news-item">
        <div class="thumb news-a" role="img" aria-label="Students gathered at a campus event"></div>
        <p class="date">November 22, 2014</p>
        <p class="copy">Lorem ipsum dolor sit amet, consectetur adipiscing elit. Aenean et dignissim sem.</p>
        <p class="more">Read More »</p>
      </div>
      <div class="news-item">
        <div class="thumb news-b" role="img" aria-label="Classroom session in progress"></div>
        <p class="date">November 22, 2014</p>
        <p class="copy">Lorem ipsum dolor sit amet, consectetur adipiscing elit. Aenean et dignissim sem.</p>
        <p class="more">Read More »</p>
      </div>
    </div>
  </div>
</section>

<section class="contact">
  <div class="contact-head">
    <svg width="54" height="54" viewBox="0 0 54 54"><circle cx="27" cy="27" r="25" fill="none" stroke="#fff" stroke-width="2"/><rect x="15" y="19" width="24" height="17" fill="#fff"/><path d="M15 19l12 10 12-10" fill="none" stroke="#1c2b5e" stroke-width="2"/></svg>
    <h2>Contact Us</h2>
    <p>Please, Feel free to contact anytime. It's always<br>a pleasure meeting new student.</p>
  </div>
  <div class="contact-cols">
    <div class="question">
      <h3>Drop Your Question</h3>
      <div class="field">Name</div>
      <div class="field">Email</div>
      <div class="field">Subject</div>
      <div class="field message">Message</div>
      <span class="send">Send</span>
    </div>
    <div class="location">
      <h3>Location Map</h3>
      <div class="map" role="img" aria-label="Street map with a pin marking the college"></div>
    </div>
    <div class="find">
      <h3>Find Us</h3>
      <div class="find-row"><svg width="14" height="18" viewBox="0 0 14 18"><path d="M7 0a7 7 0 0 0-7 7c0 5 7 11 7 11s7-6 7-11a7 7 0 0 0-7-7z" fill="#fff"/><circle cx="7" cy="7" r="2.5" fill="#1c2b5e"/></svg><span>123 Cedar Ridge Road,<br>Millbrook, BC V2X 4K8</span></div>
      <div class="find-row"><svg width="14" height="14" viewBox="0 0 14 14"><path d="M3 0l3 3-2 2a9 9 0 0 0 5 5l2-2 3 3-2 3C6 14 0 8 0 3z" fill="#fff"/></svg><span>(555) 014 - 2290</span></div>
      <div class="find-row"><svg width="14" height="14" viewBox="0 0 14 14"><path d="M3 0l3 3-2 2a9 9 0 0 0 5 5l2-2 3 3-2 3C6 14 0 8 0 3z" fill="#fff"/></svg><span>(555) 014 - 2291</span></div>
      <div class="find-row"><svg width="14" height="12" viewBox="0 0 14 12"><rect width="14" height="12" fill="#fff"/><path d="M0 0l7 6 7-6" fill="none" stroke="#1c2b5e" stroke-width="1.5"/></svg><span>info@cedarvaleridge.ca</span></div>
      <div class="socials"><span></span><span></span><span></span><span></span></div>
    </div>
  </div>
</section>

<footer class="site-footer">Copyright © 2014 CedarvaleRidge.ca . All Right Reserved</footer>

</body>
</html>
```